" a empresa trabalha na area de divulgação, e marketing usando a ferramenta instagram e facebook, usando o perfil de seus clientes, transformando em e-commerce, é tambem atua na area de vendas de paineis de led em acrilico "

```html
<!DOCTYPE html>
<html lang="pt">
<head>
<meta charset="utf-8">
<title>Lumora – Cartão de visita</title>
<link rel="stylesheet" href="https://fonts.googleapis.com/css2?family=Montserrat:wght@400;500&display=swap">
<style>
  :root {
    --backdrop: #eceef1;
    --card-pink: #d7779f;
    --card-rose: #c75489;
    --card-magenta: #a8356d;
    --card-plum: #6f2c58;
    --card-edge: #9c2f5f;
    --ink-light: rgba(255, 255, 255, 0.9);
    --band-white: rgba(255, 255, 255, 0.88);
  }
  html, body {
    margin: 0;
    padding: 0;
    width: 1200px;
    height: 1200px;
    overflow: hidden;
    background: var(--backdrop);
  }
  .canvas {
    position: relative;
    width: 1200px;
    height: 1200px;
  }
  .business-card {
    position: absolute;
    left: 100px;
    top: 317px;
    width: 1000px;
    height: 566px;
    border-radius: 28px;
    overflow: hidden;
    border: 3px solid var(--card-edge);
    box-sizing: border-box;
    box-shadow: 0 18px 40px rgba(60, 20, 45, 0.18);
  }
  .card-texture {
    position: absolute;
    inset: 0;
    background:
      radial-gradient(ellipse at 38% 35%, var(--card-pink) 0%, rgba(215, 119, 159, 0) 60%),
      linear-gradient(135deg, var(--card-rose) 0%, var(--card-magenta) 55%, var(--card-plum) 100%);
  }
  .card-bands {
    position: absolute;
    inset: 0;
    width: 100%;
    height: 100%;
  }
  .brand-block {
    position: absolute;
    left: 377px;
    top: 180px;
    transform: translateX(-50%);
    display: flex;
    flex-direction: column;
    align-items: center;
    font-family: "Montserrat", sans-serif;
    color: var(--ink-light);
  }
  .brand-square {
    width: 38px;
    height: 38px;
    border: 3px solid var(--ink-light);
    box-sizing: border-box;
    margin-bottom: 96px;
  }
  .brand-name {
    margin: 0;
    font-weight: 500;
    font-size: 60px;
    letter-spacing: 5px;
    line-height: 1;
  }
  .brand-tagline {
    margin: 14px 0 0;
    font-weight: 400;
    font-size: 14px;
    letter-spacing: 0.6px;
    white-space: nowrap;
  }
</style>
</head>
<body>
<main class="canvas">
  <section class="business-card">
    <div class="card-texture" role="img" aria-label="Textura facetada em tons de rosa e magenta"></div>
    <svg class="card-bands" viewBox="0 0 412 233" preserveAspectRatio="none" aria-hidden="true">
      <g stroke="var(--band-white)" stroke-width="9" stroke-linecap="butt" fill="none">
        <line x1="-5" y1="82" x2="85" y2="-8"/>
        <line x1="218" y1="-4" x2="420" y2="198"/>
        <line x1="420" y1="58" x2="242" y2="236"/>
      </g>
    </svg>
    <div class="brand-block">
      <div class="brand-square" aria-hidden="true"></div>
      <h1 class="brand-name">LUMORA</h1>
      <p class="brand-tagline">MARKETING DIGITAL E COMUNICAÇÃO VISUAL</p>
    </div>
  </section>
</main>
</body>
</html>
```